SkyvornQ Business Cards and Stationary Design

Need a design for our business cards and stationary. I want to carry on the theme of the logo. I want the business cards to have a design on the back. I would like the business cards and the stationary to carry the same theme, design scheme, and branding

Target Market(s)

Airlines and Maintenance Facilities

Industry/Entity Type

Aviation

Contact Information for Business Card

Name
Position Title
Address: 4827 Trellis Hollow Road, Fort Pierce, Florida, 34951
Office Number
Mobile Number
Email
Website

Font styles to use
Serif
Sans Serif

Colors

Designer to choose colors to be used in the design.

```html
<!DOCTYPE html>
<html lang="en">
<head>
<meta charset="utf-8">
<title>SkyvornQ Business Card</title>
<link href="https://fonts.googleapis.com/css2?family=Montserrat:wght@800&family=Work+Sans:wght@400;500;600&display=swap" rel="stylesheet">
<style>
  :root {
    --navy: #162c5a;
    --navy-deep: #112349;
    --white: #ffffff;
    --ink: #2b2f3a;
    --faint: #efefef;
    --stage: #2a2a2c;
  }
  * { margin: 0; padding: 0; box-sizing: border-box; }
  html, body { width: 1200px; height: 800px; overflow: hidden; }
  body {
    background: var(--stage);
    font-family: "Work Sans", Arial, sans-serif;
    position: relative;
  }
  .card {
    position: absolute;
    left: 320px;
    width: 560px;
    height: 320px;
    border-radius: 18px;
    overflow: hidden;
  }
  .card--front { top: 40px; background: linear-gradient(135deg, var(--navy) 0%, var(--navy-deep) 100%); }
  .card--back { top: 440px; background: var(--white); }

  .front__ring {
    position: absolute;
    left: 90px; top: -10px;
    width: 340px; height: 340px;
    border-radius: 50%;
    border: 34px solid rgba(255,255,255,0.05);
  }
  .brand {
    position: absolute;
    left: 0; right: 0; top: 128px;
    display: flex; align-items: center; justify-content: center; gap: 18px;
  }
  .brand__dot {
    width: 42px; height: 42px; border-radius: 50%;
    border: 6px solid var(--white);
  }
  .brand__name {
    font-family: "Montserrat", Arial, sans-serif;
    font-weight: 800;
    font-size: 46px;
    letter-spacing: 8px;
    color: var(--white);
  }
  .front__web {
    position: absolute;
    right: 120px; top: 212px;
    font-weight: 600; font-size: 15px; color: var(--white);
  }

  .back__ring {
    position: absolute;
    left: 350px; top: 50px;
    width: 200px; height: 200px;
    border-radius: 50%;
    border: 16px solid var(--faint);
  }
  .name-tab {
    position: absolute;
    left: 0; top: 70px;
    width: 330px; height: 96px;
    background: var(--navy);
    border-radius: 0 48px 48px 0;
    padding: 22px 0 0 34px;
    color: var(--white);
  }
  .name-tab__name { font-size: 30px; font-weight: 500; letter-spacing: 0.5px; line-height: 1.1; }
  .name-tab__title { font-size: 15px; font-weight: 400; margin-top: 4px; }
  .address {
    position: absolute;
    left: 60px; top: 186px;
    font-size: 13px; line-height: 1.35; color: var(--ink);
  }
  .contacts {
    position: absolute;
    left: 60px; top: 238px;
    list-style: none;
    font-size: 13px; line-height: 1.25; color: var(--ink);
  }
  .contacts li { display: flex; align-items: center; gap: 12px; }
  .contacts svg { width: 11px; height: 11px; flex: none; }
  .contacts strong { color: var(--navy); font-weight: 600; }
</style>
</head>
<body>
  <section class="card card--front">
    <div class="front__ring"></div>
    <div class="brand">
      <span class="brand__dot"></span>
      <span class="brand__name">SKYVORNQ</span>
    </div>
    <div class="front__web">www.skyvornq.com</div>
  </section>

  <section class="card card--back">
    <div class="back__ring"></div>
    <div class="name-tab">
      <div class="name-tab__name">MARCUS DELANE</div>
      <div class="name-tab__title">Co-Owner</div>
    </div>
    <address class="address" style="font-style:normal">
      4827 Trellis Hollow Road,<br>Fort Pierce,<br>Florida, 34951
    </address>
    <ul class="contacts">
      <li><svg viewBox="0 0 12 12"><rect x="3" y="0.5" width="6" height="11" rx="1.2" fill="none" stroke="#2b2f3a" stroke-width="1.3"/></svg>(772) 418-3065</li>
      <li><svg viewBox="0 0 12 12"><path d="M2 1 L4.5 1 L5.5 3.8 L4 5 Q5 7.5 7 8 L8.2 6.5 L11 7.5 L11 10 Q6 11.5 2.5 7 Q0.5 4 2 1Z" fill="#2b2f3a"/></svg>1-888-307-5142 (Toll Free)</li>
      <li><svg viewBox="0 0 12 12"><rect x="0.7" y="2" width="10.6" height="8" fill="none" stroke="#2b2f3a" stroke-width="1.3"/><path d="M1 2.5 L6 6.5 L11 2.5" fill="none" stroke="#2b2f3a" stroke-width="1.2"/></svg>info@skyvornq.com</li>
      <li><svg viewBox="0 0 12 12"><circle cx="6" cy="6" r="5.2" fill="none" stroke="#2b2f3a" stroke-width="1.2"/><path d="M1 6 H11 M6 0.8 Q3 6 6 11.2 M6 0.8 Q9 6 6 11.2" fill="none" stroke="#2b2f3a" stroke-width="1"/></svg>www.<strong>skyvornq</strong>.com</li>
    </ul>
  </section>
</body>
</html>
```